Business Card Design for a Personal Trainer

I need a business card design for my job as a personal trainer. It should have a unique, modern and exclusive design. On the front there should be only my logo with my name and my job. 0162/3819204 Tobias Lendhart Wiesengrundweg 14 80417 Munich Germany The most important contact information is the web adress. it can be bigger than the rest, but its not necessary. The card should be 8,5cmx5,5cm big. Font: Roboto. Colors: black, white, gray, 56c1ff.

```html
<!DOCTYPE html>
<html lang="de">
<head>
<meta charset="utf-8">
<title>Tobias Lendhart – Personal Trainer Visitenkarte</title>
<link rel="stylesheet" href="https://fonts.googleapis.com/css2?family=Roboto:wght@400;500&family=Open+Sans:wght@400;600&display=swap">
<style>
  :root {
    --page-bg: #3a3a3a;
    --card-black: #000000;
    --gray-light: #8a8a8a;
    --gray-mid: #5a5a5a;
    --gray-dark: #2e2e2e;
    --white: #f2f2f2;
    --accent: #3fb4e0;
    --card-edge: #d8d8d8;
  }
  * { margin: 0; padding: 0; box-sizing: border-box; }
  html, body {
    width: 1200px; height: 1200px; overflow: hidden;
    background: var(--page-bg);
  }
  .canvas { position: relative; width: 1200px; height: 1200px; }
  .card {
    position: absolute; left: 246px; width: 708px; height: 402px;
    border-radius: 22px; border: 2px solid var(--card-edge);
    overflow: hidden;
  }
  .card--front {
    top: 150px;
    background: radial-gradient(ellipse 70% 85% at 50% 0%, var(--gray-light) 0%, var(--gray-mid) 45%, var(--gray-dark) 100%);
  }
  .card--back { top: 626px; background: var(--card-black); }

  .brand {
    position: absolute; display: flex; flex-direction: column; align-items: center;
    font-family: "Roboto", sans-serif; color: var(--white);
  }
  .brand__square { width: 34px; height: 34px; background: var(--white); margin-bottom: 22px; }
  .brand__name { font-weight: 400; font-size: 31px; letter-spacing: 1px; line-height: 1; }
  .brand__role { margin-top: 8px; font-size: 12px; letter-spacing: 4px; line-height: 1; }

  .card--front .brand { left: 0; right: 0; top: 108px; }
  .website {
    position: absolute; left: 0; right: 0; top: 304px; text-align: center;
    font-family: "Open Sans", sans-serif; font-size: 33px; color: var(--accent);
  }

  .portrait {
    position: absolute; left: 30px; top: 40px; width: 216px; height: 362px;
    background: linear-gradient(180deg, #6a6a6a 0%, #3c3c3c 55%, #1a1a1a 100%);
    border-radius: 90px 90px 0 0;
  }
  .card--back .brand { left: 354px; width: 302px; top: 70px; }
  .card--back .brand__square { margin-bottom: 18px; }
  .card--back .brand__name { font-size: 30px; }

  .contact { position: absolute; font-family: "Open Sans", sans-serif; color: var(--white); }
  .contact__title {
    position: absolute; left: 264px; width: 392px; top: 220px;
    display: flex; align-items: flex-end; gap: 8px;
  }
  .contact__rule { flex: 1; height: 2px; background: var(--white); margin-bottom: 5px; }
  .contact__name { font-weight: 600; font-size: 22px; color: var(--accent); line-height: 1.2; }
  .contact__row {
    position: absolute; right: 50px; display: flex; align-items: center; gap: 12px;
    font-size: 16px;
  }
  .contact__row svg { width: 16px; height: 16px; }
  .contact__row--phone { top: 266px; }
  .contact__row--mail { top: 290px; }
  .contact__address { position: absolute; left: 282px; top: 329px; font-size: 17.5px; }
</style>
</head>
<body>
<main class="canvas">
  <section class="card card--front">
    <div class="brand">
      <span class="brand__square"></span>
      <span class="brand__name">TOBIAS LENDHART</span>
      <span class="brand__role">PERSONAL TRAINER</span>
    </div>
    <p class="website">www.lendhart-training.de</p>
  </section>

  <section class="card card--back">
    <div class="portrait" role="img" aria-label="Schwarz-weiß Porträt des Trainers mit verschränkten Armen"></div>
    <div class="brand">
      <span class="brand__square"></span>
      <span class="brand__name">TOBIAS LENDHART</span>
      <span class="brand__role">PERSONAL TRAINER</span>
    </div>
    <div class="contact contact__title">
      <span class="contact__rule"></span>
      <span class="contact__name">Tobias Lendhart</span>
    </div>
    <div class="contact contact__row contact__row--phone">
      <span>0162/3819204</span>
      <svg viewBox="0 0 24 24" aria-hidden="true"><path fill="#f2f2f2" d="M6.6 10.8a15 15 0 0 0 6.6 6.6l2.2-2.2a1 1 0 0 1 1-.25 11.4 11.4 0 0 0 3.6.57 1 1 0 0 1 1 1V20a1 1 0 0 1-1 1A17 17 0 0 1 3 4a1 1 0 0 1 1-1h3.5a1 1 0 0 1 1 1c0 1.25.2 2.45.57 3.57a1 1 0 0 1-.25 1z"/></svg>
    </div>
    <div class="contact contact__row contact__row--mail">
      <span>t.lendhart@postfach.de</span>
      <svg viewBox="0 0 24 24" aria-hidden="true"><rect x="2" y="5" width="20" height="14" fill="#f2f2f2"/><path d="M2 5l10 8 10-8" fill="none" stroke="#000" stroke-width="1.6"/></svg>
    </div>
    <p class="contact contact__address">Wiesengrundweg 14 , 80417 München</p>
  </section>
</main>
</body>
</html>
```